Varlomatch E-commerce Website Design

I'm looking into having my e-comm website built. We are an investment company that is investing in a private label focused on a rising sport category called Pickleball in EU market.

We will provide top quality material and acessories for players be ready to go to courts. We will have a range of: Rackets, Set of balls, Net, Lines, overgrip, water bottle, player bag.

As it´s a new sports category we would like to see an architecture that alows us to share some storytelling about the category, the brand and lead to purchase of our products.

We will position our self as an inclusive and fun brand that you can reach out to find more info about Pickleball Sport, buy your pickleball stuff and have fun. Its all about action and fun.

Target Market(s)

Europe Market

Industry/Entity Type

Pickleball (Sports)

Coding

Coded - Design and coding required

Number of Pages Required

1 page

Requirements
Must have
• E-commerce look and feel
Nice to have
• A bit of storytelling about the brand and specially the category (Pickleball).

```html
<!DOCTYPE html>
<html lang="en">
<head>
<meta charset="utf-8">
<title>Varlomatch — Pickleball Gear</title>
<link rel="stylesheet" href="https://fonts.googleapis.com/css2?family=Krona+One&family=Poppins:ital,wght@0,400;0,500;0,600;1,400&display=swap">
<style>
:root{
  --red:#a4232d;
  --blue:#213b87;
  --ink:#1b1b1b;
  --muted:#555;
  --line:#e3e3e3;
  --footer:#161616;
  --star:#f2a20c;
  --white:#fff;
}
*{box-sizing:border-box;margin:0;padding:0}
html,body{width:1200px;height:4785px;overflow:hidden}
body{font-family:"Poppins",sans-serif;color:var(--ink);background:var(--white);font-size:14px;position:relative}
.wrap{width:1000px;margin:0 auto;position:relative}
.btn{display:inline-block;background:var(--red);color:var(--white);font-size:14px;font-weight:600;padding:10px 28px;border-radius:3px;text-transform:uppercase;letter-spacing:.5px}
.block{position:absolute;left:0;width:1200px}

/* top bar */
.topbar{height:34px;background:var(--red);color:var(--white);font-size:11px;display:flex;align-items:center}
.topbar .wrap{display:flex;justify-content:flex-end;gap:80px}
.topbar b{font-weight:600}

/* header */
.header{height:70px;border-bottom:1px solid var(--line)}
.header .wrap{display:flex;align-items:center;height:70px}
.logo{font-family:"Krona One",sans-serif;font-size:24px;text-transform:uppercase;color:var(--ink)}
.search{margin-left:178px;display:flex;height:32px;width:435px}
.search .field{flex:1;border:1px solid #ccc;border-right:0;border-radius:3px 0 0 3px;display:flex;align-items:center;padding-left:12px;gap:8px;color:#999;font-size:12px}
.search .go{background:var(--red);color:var(--white);font-size:12px;font-weight:600;padding:0 20px;display:flex;align-items:center;border-radius:0 3px 3px 0}
.header-links{margin-left:auto;display:flex;gap:16px;font-size:14px;align-items:center}
.header-links span{display:flex;align-items:center;gap:4px}

/* nav */
.nav{height:48px;border-bottom:1px solid var(--line)}
.nav ul{list-style:none;display:flex;justify-content:space-between;height:48px;align-items:center;font-size:14px;font-weight:500}
.nav li.active{color:var(--red);border-bottom:2px solid var(--red);padding-bottom:2px}

/* hero */
.hero{top:152px;height:624px;background:
  radial-gradient(ellipse 260px 200px at 720px 300px,rgba(120,150,210,.75),transparent 70%),
  radial-gradient(ellipse 200px 150px at 640px 420px,rgba(70,60,50,.6),transparent 70%),
  linear-gradient(180deg,#5d7a4c 0%,#6f7f5a 22%,#3f5e54 40%,#4c5d5a 55%,#8c4540 70%,#a24f47 85%,#873a36 100%)}
.hero-copy{position:absolute;left:106px;top:205px;color:var(--white)}
.hero-copy h1{font-family:"Krona One",sans-serif;font-size:44px;font-weight:400;text-transform:uppercase;margin-bottom:12px;letter-spacing:1px}
.hero-copy p{font-size:18px;line-height:32px;width:400px;margin-bottom:22px}
.hero .arrow{position:absolute;top:310px;transform:translateY(-50%)}
.hero .dots{position:absolute;bottom:36px;left:0;right:0;display:flex;justify-content:center;gap:18px}
.hero .dots i{width:11px;height:11px;border-radius:50%;background:rgba(255,255,255,.5)}
.hero .dots i.on{background:var(--white)}

/* headings */
.sec-title{text-align:center;font-size:36px;font-family:"Krona One",sans-serif;font-weight:400;text-transform:uppercase}
.sec-sub{text-align:center;font-size:14px;color:var(--muted);line-height:28px;margin-top:12px}

/* categories */
.categories{top:862px}
.cat-row{position:relative;margin-top:28px;display:flex;gap:19px}
.cat{width:236px;height:298px;border-radius:8px;overflow:hidden;box-shadow:0 2px 8px rgba(0,0,0,.18);background:var(--white)}
.cat .photo{height:250px}
.cat h3{font-family:"Krona One",sans-serif;font-weight:400;font-size:17px;text-align:center;line-height:48px;text-transform:uppercase}
.circle-arrow{position:absolute;top:126px;width:42px;height:42px;border-radius:50%;background:var(--white);box-shadow:0 1px 6px rgba(0,0,0,.25);display:flex;align-items:center;justify-content:center}
.cat-cta{text-align:center;margin-top:38px}

/* about */
.about{top:1464px;height:531px;background:var(--blue)}
.about .photo{position:absolute;left:0;top:0;width:620px;height:531px;background:
  radial-gradient(ellipse 130px 200px at 380px 250px,rgba(235,235,235,.85),transparent 70%),
  radial-gradient(ellipse 200px 180px at 80px 200px,rgba(222,160,80,.8),transparent 70%),
  linear-gradient(180deg,#2c4d9c 0%,#2a4a96 62%,#9a7b5e 72%,#a58466 100%)}
.about-copy{position:absolute;left:670px;top:104px;width:430px;color:var(--white)}
.about-copy h2{font-family:"Krona One",sans-serif;font-weight:400;font-size:33px;margin-bottom:22px}
.about-copy p{font-size:14px;line-height:31.5px;margin-bottom:26px}

/* products */
.products{top:2076px}
.tabs{display:flex;justify-content:center;gap:24px;margin-top:22px;font-size:13px;font-weight:500}
.tabs span{padding:5px 16px}
.tabs .on{color:var(--red);border:1px solid var(--red);border-radius:2px}
.grid{display:grid;grid-template-columns:repeat(4,236px);gap:19px 19px;margin-top:24px}
.product .photo{height:270px;border:1px solid var(--line)}
.product .price{color:var(--red);font-size:20px;font-weight:600;text-align:center;margin-top:12px}
.product p{font-size:13px;text-align:center;line-height:20px;margin-top:6px}
.stars{color:var(--star);font-size:11px;letter-spacing:1px;line-height:14px;text-align:center;margin-top:4px}

/* gallery */
.gallery{top:3065px;height:731px}
.gallery .photo{position:absolute}

/* testimonials */
.testimonials{top:3870px}
.quote{position:absolute;background:var(--white);box-shadow:0 2px 12px rgba(0,0,0,.15);padding:32px 22px;font-style:italic;font-size:13px;line-height:27px;color:var(--muted);text-align:center;width:312px}
.quote::after{content:"";position:absolute;width:22px;height:22px;background:var(--white);transform:rotate(45deg)}
.quote.down::after{bottom:-11px;left:60px;box-shadow:3px 3px 4px rgba(0,0,0,.08)}
.quote.up::after{top:-11px;left:200px;box-shadow:-3px -3px 4px rgba(0,0,0,.06)}
.author{position:absolute;display:flex;align-items:center;gap:12px;font-size:14px;font-weight:500}
.author .stars{text-align:left;margin-top:0}
.avatar{width:58px;height:58px;border-radius:50%;background:linear-gradient(135deg,#d8c8b8,#8d7b6c)}

/* footer */
.footer{top:4388px;height:397px;background:var(--footer);color:var(--white)}
.footer .logo{color:var(--white);position:absolute;left:100px;top:80px}
.f-about{position:absolute;left:100px;top:124px;width:300px;font-size:12px;line-height:26px}
.social{position:absolute;left:100px;top:262px;display:flex;gap:10px}
.social i{width:38px;height:38px;border:1.5px solid var(--white);border-radius:50%;display:block}
.f-col{position:absolute;top:86px;font-size:14px;line-height:35px}
.f-col h4{font-size:15px;font-weight:600;line-height:20px;margin-bottom:10px;text-transform:uppercase}
.f-contact ul{list-style:none}
.f-contact li{display:flex;gap:8px;line-height:26px;margin-bottom:8px}
.copy{position:absolute;left:100px;top:352px;font-size:14px}
.pay{position:absolute;right:100px;top:348px;display:flex;gap:8px}
.pay span{width:40px;height:22px;border-radius:3px;background:#e9e9e9;color:var(--ink);font-size:8px;font-weight:600;display:flex;align-items:center;justify-content:center}
</style>
</head>
<body>

<div class="topbar">
  <div class="wrap">
    <span>In Stock Orders Ship Same Day (order by 12pm CET M-F)</span>
    <span><b>(800) 555-0142</b> M-F 8:30am-5pm CET</span>
  </div>
</div>

<header class="header">
  <div class="wrap">
    <div class="logo">Varlomatch</div>
    <div class="search">
      <div class="field">
        <svg width="14" height="14" viewBox="0 0 14 14"><circle cx="6" cy="6" r="4.5" fill="none" stroke="#555" stroke-width="1.5"/><line x1="9.5" y1="9.5" x2="13" y2="13" stroke="#555" stroke-width="1.5"/></svg>
        Find it here...
      </div>
      <div class="go">SEARCH</div>
    </div>
    <div class="header-links">
      <span><svg width="12" height="12" viewBox="0 0 12 12"><circle cx="6" cy="3.5" r="3" fill="#222"/><path d="M0 12c0-4 2.5-5.5 6-5.5S12 8 12 12z" fill="#222"/></svg>Account</span>
      <span><svg width="16" height="13" viewBox="0 0 16 13"><path d="M1 4h14l-2 8H3z" fill="none" stroke="var(--red)" stroke-width="1.5"/><path d="M5 4l3-3 3 3" fill="none" stroke="#222" stroke-width="1.3"/></svg>Cart</span>
    </div>
  </div>
</header>

<nav class="nav">
  <div class="wrap">
    <ul>
      <li class="active">HOME</li><li>ABOUT</li><li>RACKETS</li><li>SET OF BALLS</li><li>NET</li><li>LINES</li><li>OVERGRIP</li><li>WATER BOTTLE</li><li>PLAYER BAG</li><li>CONTACT</li>
    </ul>
  </div>
</nav>

<section class="block hero" role="img" aria-label="Pickleball player lunging to return a ball at the net on an outdoor court">
  <svg class="arrow" style="left:56px" width="26" height="46" viewBox="0 0 26 46"><path d="M24 2L3 23l21 21" fill="none" stroke="#fff" stroke-width="2"/></svg>
  <svg class="arrow" style="right:56px" width="26" height="46" viewBox="0 0 26 46"><path d="M2 2l21 21L2 44" fill="none" stroke="#fff" stroke-width="2"/></svg>
  <div class="hero-copy">
    <h1>Varlomatch</h1>
    <p>Lorem ipsum dolor sit amet, consectetur adipiscing elit, sed do eiusmod</p>
    <span class="btn">Shop Now</span>
  </div>
  <div class="dots"><i></i><i></i><i class="on"></i><i></i></div>
</section>

<section class="block categories">
  <div class="wrap">
    <h2 class="sec-title">Shop by Category</h2>
    <p class="sec-sub">Sed ut perspiciatis unde omnis iste natus error sit voluptatem accusantium doloremque laudantium,<br>totam rem aperiam, eaque ipsa quae ab illo inventore veritatis</p>
    <div class="cat-row">
      <div class="circle-arrow" style="left:-58px"><svg width="22" height="12" viewBox="0 0 22 12"><path d="M21 6H2M7 1L2 6l5 5" fill="none" stroke="#222" stroke-width="1.6"/></svg></div>
      <div class="cat"><div class="photo" role="img" aria-label="Tennis racket and balls on a grass court" style="background:radial-gradient(circle at 120px 140px,#d4e24a 0,#c0383a 45px,transparent 110px),linear-gradient(160deg,#7aa44a,#5f8f37 60%,#dfe4da)"></div><h3>Rackets</h3></div>
      <div class="cat"><div class="photo" role="img" aria-label="Assorted sports balls on grass" style="background:radial-gradient(circle at 70px 70px,#f2f2f2 0,#2a2a2a 60px,transparent 90px),radial-gradient(circle at 180px 200px,#e8e2d8,transparent 60px),linear-gradient(160deg,#4a6b2c,#7ea14a)"></div><h3>Set of Balls</h3></div>
      <div class="cat"><div class="photo" role="img" aria-label="Black insulated water bottle on a pebbled surface" style="background:linear-gradient(90deg,transparent 35%,#2c2c2c 40%,#3a3a3a 58%,transparent 63%),linear-gradient(180deg,#c9b392,#a89274 60%,#6e5d47)"></div><h3>Water Bottle</h3></div>
      <div class="cat"><div class="photo" role="img" aria-label="Hand wrapping white overgrip tape" style="background:radial-gradient(ellipse 110px 90px at 110px 130px,#e9b79c,transparent 75%),linear-gradient(160deg,#c46a34,#d99570 40%,#f1ece8)"></div><h3>Overgrip</h3></div>
      <div class="circle-arrow" style="right:-58px"><svg width="22" height="12" viewBox="0 0 22 12"><path d="M1 6h19M15 1l5 5-5 5" fill="none" stroke="#222" stroke-width="1.6"/></svg></div>
    </div>
    <div class="cat-cta"><span class="btn" style="font-size:13px;padding:10px 26px">View All Categories</span></div>
  </div>
</section>

<section class="block about">
  <div class="photo" role="img" aria-label="Softball catcher crouching in protective gear in front of a stadium wall"></div>
  <div class="about-copy">
    <h2>ABOUT US</h2>
    <p>Sed ut perspiciatis unde omniit voluptatem accusantium doloremque laudam, tom riam, ee ipsaaab illo inventore veritatis et quasi architecto be vitae dicta sunt explicabo. Nemo enim ipsam volupem quia voluptas sit aspernatur aut odit aut fugit, sed quiconsequuntur magni dolores eos qui ratione voluptatem</p>
    <span class="btn" style="font-size:13px;padding:10px 26px">Learn More</span>
  </div>
</section>

<section class="block products">
  <div class="wrap">
    <h2 class="sec-title">Our Products</h2>
    <div class="tabs"><span class="on">Best Sellers</span><span>New Products</span><span>Sales Products</span></div>
    <div class="grid">
      <div class="product"><div class="photo" role="img" aria-label="Purple pickleball paddle with orange ball" style="background:radial-gradient(ellipse 70px 95px at 50% 45%,#b58aa6,#8c7aa0 55%,transparent 100%),#fff"></div><div class="price">€ 24,80</div><p>At vero eos et accusamus<br>et iusto odio dnissimos</p><div class="stars">★★★★★</div></div>
      <div class="product"><div class="photo" role="img" aria-label="Pair of turquoise tennis rackets with a ball" style="background:radial-gradient(ellipse 70px 110px at 50% 45%,#6fd0cf,#2ba6b0 55%,transparent 100%),#fff"></div><div class="price">€ 24,80</div><p>At vero eos et accusamus<br>et iusto odio dnissimos</p><div class="stars">★★★★★</div></div>
      <div class="product"><div class="photo" role="img" aria-label="Rolls of black overgrip tape" style="background:radial-gradient(ellipse 100px 45px at 50% 50%,#3a3a3a,#1e1e1e 55%,transparent 100%),#fff"></div><div class="price">€ 24,80</div><p>At vero eos et accusamus<br>et iusto odio dnissimos</p><div class="stars">★★★★★</div></div>
      <div class="product"><div class="photo" role="img" aria-label="Lime green sports water bottle" style="background:radial-gradient(ellipse 50px 110px at 50% 50%,#a8d845,#7bb324 55%,transparent 100%),#fff"></div><div class="price">€ 24,80</div><p>At vero eos et accusamus<br>et iusto odio dnissimos</p><div class="stars">★★★★★</div></div>
      <div class="product"><div class="photo" role="img" aria-label="Yellow and black tennis racket" style="background:radial-gradient(ellipse 80px 120px at 50% 45%,#e8ec9a,#5a5a3a 60%,transparent 100%),#fff"></div><div class="price">€ 24,80</div><p>At vero eos et accusamus<br>et iusto odio dnissimos</p><div class="stars">★★★★★</div></div>
      <div class="product"><div class="photo" role="img" aria-label="Yellow tennis ball" style="background:radial-gradient(circle at 50% 48%,#e6f36a,#bfd12a 55px,transparent 90px),#fff"></div><div class="price">€ 24,80</div><p>At vero eos et accusamus<br>et iusto odio dnissimos</p><div class="stars">★★★★★</div></div>
      <div class="product"><div class="photo" role="img" aria-label="Purple pickleball paddle with orange ball" style="background:radial-gradient(ellipse 70px 95px at 50% 45%,#b58aa6,#8c7aa0 55%,transparent 100%),#fff"></div><div class="price">€ 24,80</div><p>At vero eos et accusamus<br>et iusto odio dnissimos</p><div class="stars">★★★★★</div></div>
      <div class="product"><div class="photo" role="img" aria-label="Brown leather player bag" style="background:radial-gradient(ellipse 100px 65px at 50% 52%,#6e4a32,#4a2e1d 55%,transparent 100%),#fff"></div><div class="price">€ 24,80</div><p>At vero eos et accusamus<br>et iusto odio dnissimos</p><div class="stars">★★★★★</div></div>
    </div>
  </div>
</section>

<section class="block gallery">
  <div class="photo" role="img" aria-label="Tennis balls on a clay court" style="left:0;top:22px;width:435px;height:350px;background:radial-gradient(ellipse 140px 60px at 220px 190px,#d6e24a,transparent 80%),linear-gradient(180deg,#4d7a6a 0%,#6c8a78 22%,#b86a3e 42%,#a8512b 70%,#8e3f22 100%)"></div>
  <div class="photo" role="img" aria-label="Racket and ball on a green court line" style="left:444px;top:0;width:310px;height:353px;background:linear-gradient(150deg,#2b3b2e 0%,#3f7a4e 35%,#4f8a5c 55%,#eef1ea 60%,#eef1ea 64%,#3f7a4e 70%,#376e46 100%)"></div>
  <div class="photo" role="img" aria-label="Football player kicking a ball on a pitch" style="left:765px;top:22px;width:435px;height:350px;background:linear-gradient(180deg,#6d94c0 0%,#aac2da 30%,#d9e1e8 50%,#4d8a3f 62%,#2f6a2c 100%)"></div>
  <div class="photo" role="img" aria-label="Tennis player serving on a hard court" style="left:0;top:381px;width:435px;height:350px;background:linear-gradient(180deg,#f1f4f6 0%,#c7dbe6 35%,#2f6f6a 62%,#275a52 75%,#1f4c6a 100%)"></div>
  <div class="photo" role="img" aria-label="Table tennis paddles and balls on a table" style="left:444px;top:364px;width:310px;height:367px;background:radial-gradient(ellipse 120px 60px at 160px 250px,#e0623a,transparent 80%),linear-gradient(170deg,#22302a 0%,#4a4630 35%,#d8d8d4 55%,#c9c9c5 100%)"></div>
  <div class="photo" role="img" aria-label="Man playing table tennis indoors" style="left:765px;top:381px;width:435px;height:350px;background:radial-gradient(ellipse 90px 140px at 330px 170px,#4a4a4a,transparent 80%),linear-gradient(180deg,#ece3da 0%,#dccbbd 60%,#6c5e54 85%,#3a3430 100%)"></div>
</section>

<section class="block testimonials">
  <h2 class="sec-title" style="font-size:34px;margin-top:12px">What Our Clients Say</h2>
  <div class="quote down" style="left:100px;top:91px">Sed ut perspiciatis unde omnis iste naturor sit voluptatem accusantium doloremque laudantium, totam rem m, eaque ipsa quae ab illo inventore veritatis et quasi architecto beatae vitae dicta sunt explicabo.</div>
  <div class="author" style="left:138px;top:357px"><div class="avatar" role="img" aria-label="Client portrait"></div><div>Elena Marsh<div class="stars">★★★★★</div></div></div>

  <div class="author" style="left:480px;top:91px"><div class="avatar" role="img" aria-label="Client portrait"></div><div>Elena Marsh<div class="stars">★★★★★</div></div></div>
  <div class="quote up" style="left:442px;top:188px">Sed ut perspiciatis unde omnis iste naturor sit voluptatem accusantium doloremque laudantium, totam rem m, eaque ipsa quae ab illo inventore veritatis et quasi architecto beatae vitae dicta sunt explicabo.</div>

  <div class="quote down" style="left:789px;top:91px">Sed ut perspiciatis unde omnis iste naturor sit voluptatem accusantium doloremque laudantium, totam rem m, eaque ipsa quae ab illo inventore veritatis et quasi architecto beatae vitae dicta sunt explicabo.</div>
  <div class="author" style="left:826px;top:357px"><div class="avatar" role="img" aria-label="Client portrait"></div><div>Elena Marsh<div class="stars">★★★★★</div></div></div>
</section>

<footer class="block footer">
  <div class="logo">Varlomatch</div>
  <p class="f-about">Lorem ipsum dolor sit amet, cetur adipiscing elit, sed do eiuod tempor incididunt ut labore et dolore ua. Quis ipsum suspendisse ultrices gravida. Risus commodo viverra maecenas accumsan lacus vel facilisis.</p>
  <div class="social" aria-label="Social channels"><i></i><i></i><i></i><i></i></div>
  <div class="f-col" style="left:461px"><h4>Quick Links</h4>About Us<br>Contact Us<br>Wholesale<br>FAQ<br>Policies</div>
  <div class="f-col" style="left:637px"><h4>Information</h4>Gift Packs<br>Contact Us<br>International Shipping info<br>Privacy &amp; Security<br>Satisfaction Guarantee</div>
  <div class="f-col f-contact" style="left:908px"><h4>Contact Us</h4>
    <ul>
      <li><svg width="14" height="18" viewBox="0 0 14 18" style="margin-top:4px"><path d="M7 17s6-6.5 6-10.5A6 6 0 0 0 1 6.5C1 10.5 7 17 7 17z" fill="#fff"/><circle cx="7" cy="6.5" r="2.2" fill="#161616"/></svg><span>48 Courtside Lane<br>Lisbon 1200-000</span></li>
      <li><svg width="14" height="18" viewBox="0 0 14 18" style="margin-top:4px"><path d="M7 17s6-6.5 6-10.5A6 6 0 0 0 1 6.5C1 10.5 7 17 7 17z" fill="#fff"/><circle cx="7" cy="6.5" r="2.2" fill="#161616"/></svg><span>+351 210 555 019</span></li>
      <li><svg width="14" height="18" viewBox="0 0 14 18" style="margin-top:4px"><path d="M7 17s6-6.5 6-10.5A6 6 0 0 0 1 6.5C1 10.5 7 17 7 17z" fill="#fff"/><circle cx="7" cy="6.5" r="2.2" fill="#161616"/></svg><span>hello@varlomatch.com</span></li>
    </ul>
  </div>
  <div class="copy">©Copyright ©2023 Varlomatch . All Rights Reserved.</div>
  <div class="pay"><span>PayNest</span><span>CardOne</span><span>Vexa</span><span>Amplo</span></div>
</footer>

</body>
</html>
```